Alaska Law Firm Needs a Sticker Design

We need a design for stickers to put on already-printed brochures. We mail the brochures to potential clients so they can learn more about accident-induced injuries, insurance claims, legal representation, and our own law firm.

One of our lawyers wrote a book that provides a helpful overview of personal injury claims. We are offering this book for free to anyone who calls and requests it. Therefore, the sticker design should include one of the following phrases, or something very similar:
a) "Still have questions? Call and request our book-- for free!"
b) "Still have questions about auto accident claims? Call and request our book today."
c) "Still have questions about filing a claim? Call and request a free copy of our book."
d) "Still have questions? Call us today to request a free copy of our book, Clear Lanes Ahead."
e) "To learn more about automobile accidents and insurance, call today and request a free copy of our book."

The sticker should be approximately 3"x3" and may be a circle, square, rectangle, or ellipsis. The sticker will be placed on the back of the folder, which is light blue. We would like the sticker to match the color scheme of our website and the folder.

I will upload an image of the book cover as soon as I obtain it.

Law Firm

Font styles to use
Serif
Sans Serif

Requirements
Should not have
• Bright colors that aren't already used in the folder design. e.g. no bright orange, pink, chartreuse, turquoise, yellow, red.

```html
<!DOCTYPE html>
<html lang="en">
<head>
<meta charset="utf-8">
<title>Free Book Sticker</title>
<link rel="stylesheet" href="https://fonts.googleapis.com/css2?family=Archivo:wght@500;800&family=Montserrat:wght@800&display=swap">
<style>
  :root {
    --sticker-navy: #1d3763;
    --ring-light-blue: #bcd9f0;
    --headline-sky: #9ccff4;
    --body-cream: #f3f0e3;
    --phone-white: #ffffff;
    --page-bg: #ffffff;
  }
  html, body {
    margin: 0;
    padding: 0;
    width: 1200px;
    height: 1200px;
    overflow: hidden;
    background: var(--page-bg);
  }
  .sticker {
    position: relative;
    width: 1200px;
    height: 1200px;
  }
  .sticker-shape {
    position: absolute;
    inset: 0;
  }
  .copy-line {
    position: absolute;
    left: 0;
    width: 1200px;
    margin: 0;
    text-align: center;
    line-height: 1;
    white-space: nowrap;
  }
  .headline {
    font-family: "Archivo", Arial, sans-serif;
    font-weight: 800;
    font-size: 86px;
    letter-spacing: -1px;
    color: var(--headline-sky);
  }
  .offer {
    font-family: "Archivo", Arial, sans-serif;
    font-weight: 500;
    font-size: 90px;
    letter-spacing: -0.5px;
    color: var(--body-cream);
  }
  .divider-dots {
    position: absolute;
    left: 0;
    top: 855px;
  }
  .phone-row {
    position: absolute;
    left: 0;
    width: 1200px;
    top: 916px;
    display: flex;
    justify-content: center;
    align-items: center;
    gap: 26px;
  }
  .phone-icon {
    width: 80px;
    height: 80px;
  }
  .phone-number {
    font-family: "Montserrat", Arial, sans-serif;
    font-weight: 800;
    font-size: 90px;
    line-height: 1;
    color: var(--phone-white);
    letter-spacing: 1px;
  }
</style>
</head>
<body>
  <div class="sticker">
    <svg class="sticker-shape" width="1200" height="1200" viewBox="0 0 1200 1200" aria-hidden="true">
      <circle cx="600" cy="600" r="594" fill="var(--sticker-navy)"/>
      <circle cx="600" cy="600" r="562" fill="none" stroke="var(--ring-light-blue)" stroke-width="3"/>
    </svg>

    <p class="copy-line headline" style="top:184px">To learn more</p>
    <p class="copy-line headline" style="top:276px">about automobile</p>
    <p class="copy-line headline" style="top:372px">accidents</p>
    <p class="copy-line headline" style="top:463px">and insurance,</p>

    <p class="copy-line offer" style="top:556px">Call today and</p>
    <p class="copy-line offer" style="top:650px">request a free copy</p>
    <p class="copy-line offer" style="top:743px">of our book.</p>

    <svg class="divider-dots" width="1200" height="24" viewBox="0 0 1200 24" aria-hidden="true">
      <circle cx="510" cy="12" r="7" fill="var(--headline-sky)"/>
      <circle cx="599" cy="12" r="7" fill="var(--headline-sky)"/>
      <circle cx="686" cy="12" r="7" fill="var(--headline-sky)"/>
    </svg>

    <div class="phone-row">
      <svg class="phone-icon" viewBox="0 0 80 80" aria-hidden="true">
        <circle cx="40" cy="40" r="35" fill="none" stroke="var(--phone-white)" stroke-width="4"/>
        <path d="M48 18 L56 24 Q58 26 56 29 L51 35 Q49 37 47 35 L44 33 Q36 42 33 52 L37 53 Q39 55 38 57 L34 64 Q32 66 30 65 L22 60 Q19 58 20 54 Q26 32 44 19 Q46 17 48 18 Z" fill="var(--phone-white)"/>
      </svg>
      <span class="phone-number">907.555.0142</span>
    </div>
  </div>
</body>
</html>
```